Communication and Marketing agency needs a new presentation card

We are a group of communication and marketing agencies specialized in companies that are in the logistics and industrial sector. The head agency is TELVANO Grupo and the group consists of 4 agencies: TELVANO Media, TELVANO Digital, TELVANO Research and DifundeEnPantalla. We hace 4 offices in Spain (Madrid, Barcelona, Valencia and Murcia). We are looking for a clean and attractive design that transmits our experience, brand presence in the market and knowledge to those who receive the card.It has to maintain the colors of the logo that is attached.
Target Market(s)
logistics and industrial sector
Marketing department
Contact Information for Business Card
Clean and attractive design

```html
<!DOCTYPE html>
<html lang="es">
<head>
<meta charset="utf-8">
<title>TELVANO Grupo – Tarjeta de presentación</title>
<link href="https://fonts.googleapis.com/css2?family=Open+Sans:wght@400;600;700&display=swap" rel="stylesheet">
<style>
  :root {
    --brand-red: #b21c27;
    --ink-grey: #555555;
    --rule-grey: #bdbdbd;
    --paper: #ffffff;
    --backdrop: #2a2a2a;
  }
  * { margin: 0; padding: 0; box-sizing: border-box; }
  html, body {
    width: 1125px; height: 1200px; overflow: hidden;
    background: var(--backdrop);
    font-family: "Open Sans", Arial, sans-serif;
  }
  .card {
    position: absolute; left: 150px; width: 826px; height: 472px; overflow: hidden;
  }
  .card--front { top: 98px; background: var(--paper); }
  .card--back { top: 630px; background: var(--brand-red); }

  /* front */
  .brand-mark {
    position: absolute; right: 420px; top: 190px; text-align: right;
    color: var(--brand-red); font-weight: 600; line-height: 1;
  }
  .brand-mark__name { display: block; font-size: 58px; letter-spacing: 3px; }
  .brand-mark__unit { display: block; font-size: 32px; margin-top: 6px; }
  .divider {
    position: absolute; left: 447px; top: 119px; width: 2px; height: 237px;
    background: linear-gradient(to bottom, transparent, var(--rule-grey) 15%, var(--rule-grey) 85%, transparent);
  }
  .contact { position: absolute; left: 483px; top: 130px; }
  .contact__name { color: var(--brand-red); font-size: 27px; font-weight: 700; line-height: 1.2; }
  .contact__role { color: var(--ink-grey); font-size: 20px; line-height: 1.3; margin-bottom: 8px; }
  .contact__list { list-style: none; }
  .contact__item {
    display: flex; align-items: center; height: 27px;
    color: var(--ink-grey); font-size: 19.5px;
  }
  .contact__icon { width: 20px; height: 20px; margin-right: 16px; flex: none; }
  .offices-band { position: absolute; left: 0; top: 401px; width: 797px; height: 37px; }
  .offices-band__text {
    position: absolute; left: 0; top: 401px; width: 797px; height: 37px;
    padding-right: 40px;
    display: flex; justify-content: center; align-items: center;
    color: var(--paper); font-size: 20px;
  }
  .offices-band__dot { margin: 0 9px; font-size: 14px; }

  /* back */
  .group-mark {
    position: absolute; left: 0; right: 0; top: 128px; text-align: center;
    color: var(--paper); font-weight: 600; line-height: 1;
  }
  .group-mark__name { display: block; font-size: 88px; letter-spacing: 5px; }
  .group-mark__unit { display: block; font-size: 44px; margin-top: 12px; padding-left: 280px; }
  .agency-strip {
    position: absolute; left: 0; top: 333px; width: 100%; height: 92px;
    background: var(--paper);
    display: flex; justify-content: space-around; align-items: center;
  }
  .agency {
    color: var(--brand-red); font-weight: 600; text-align: center; line-height: 1.1;
    font-size: 24px; letter-spacing: 1px;
  }
  .agency__unit { display: block; font-size: 18px; letter-spacing: 0; }
  .agency--grey { color: var(--ink-grey); }
</style>
</head>
<body>

<section class="card card--front" aria-label="Anverso de la tarjeta">
  <div class="brand-mark">
    <span class="brand-mark__name">TELVANO</span>
    <span class="brand-mark__unit">Media</span>
  </div>

  <div class="divider"></div>

  <div class="contact">
    <p class="contact__name">Lorenzo Valdés</p>
    <p class="contact__role">Director</p>
    <ul class="contact__list">
      <li class="contact__item">
        <svg class="contact__icon" viewBox="0 0 20 20" aria-hidden="true">
          <path fill="#b21c27" d="M2 8c0-3 4-5 8-5s8 2 8 5l-3 1-1-2c-2-1-6-1-8 0L5 9zM5 10h10l2 7H3z"/>
          <circle cx="10" cy="13" r="2" fill="#fff"/>
        </svg>
        910 472 618
      </li>
      <li class="contact__item">
        <svg class="contact__icon" viewBox="0 0 20 20" aria-hidden="true">
          <rect x="5" y="1" width="10" height="18" rx="2" fill="#b21c27"/>
          <rect x="7" y="4" width="6" height="10" fill="#fff"/>
        </svg>
        644 218 537
      </li>
      <li class="contact__item">
        <svg class="contact__icon" viewBox="0 0 20 20" aria-hidden="true">
          <rect x="1" y="5" width="18" height="11" fill="#b21c27"/>
          <path d="M1 5l9 6 9-6" fill="none" stroke="#fff" stroke-width="1.5"/>
        </svg>
        lvaldes@telvano.es
      </li>
      <li class="contact__item">
        <svg class="contact__icon" viewBox="0 0 20 20" aria-hidden="true">
          <rect x="2" y="3" width="15" height="15" fill="#b21c27"/>
        </svg>
        lorenzovaldes
      </li>
      <li class="contact__item">
        <svg class="contact__icon" viewBox="0 0 20 20" aria-hidden="true">
          <circle cx="10" cy="10" r="8" fill="#b21c27"/>
          <path d="M2 10h16M10 2c-3 4-3 12 0 16M10 2c3 4 3 12 0 16" fill="none" stroke="#fff" stroke-width="1"/>
        </svg>
        telvano.es
      </li>
    </ul>
  </div>

  <svg class="offices-band" viewBox="0 0 797 37" aria-hidden="true">
    <polygon points="0,0 773,0 797,37 0,37" fill="#b21c27"/>
  </svg>
  <p class="offices-band__text">
    Madrid<span class="offices-band__dot">●</span>Barcelona<span class="offices-band__dot">●</span>Valencia<span class="offices-band__dot">●</span>Murcia
  </p>
</section>

<section class="card card--back" aria-label="Reverso de la tarjeta">
  <div class="group-mark">
    <span class="group-mark__name">TELVANO</span>
    <span class="group-mark__unit">Grupo</span>
  </div>

  <div class="agency-strip">
    <p class="agency agency--grey">TELVANO<span class="agency__unit">Digital</span></p>
    <p class="agency">TELVANO<span class="agency__unit">Media</span></p>
    <p class="agency agency--grey">TELVANO<span class="agency__unit">Research</span></p>
    <p class="agency">DIFUNDE<span class="agency__unit">EnPantalla</span></p>
  </div>
</section>

</body>
</html>
```